Heron Loan Partners Business Card

We need a business card design for our mortgage servicing company. In addition to servicing the loans of homeowners, we help homeowners with purchasing their homes and any mortgage refinancing. We would like to see designs that use the colors in the logo attached below (gold-ish yellow and navy blue), and any other design you deem fit! The design should communicate a simpler life with smart mortgages provided by Heron.

```html
<!DOCTYPE html>
<html lang="en">
<head>
<meta charset="utf-8">
<title>Heron Loan Partners – Business Card</title>
<link rel="stylesheet" href="https://fonts.googleapis.com/css2?family=Open+Sans:wght@400;600;700&display=swap">
<style>
  :root {
    --backdrop: #2e2e2e;
    --gold: #e0b33f;
    --gold-deep: #c99f33;
    --navy: #231f52;
    --paper: #ffffff;
    --ink: #1d1d1f;
  }
  * { margin: 0; padding: 0; box-sizing: border-box; }
  html, body {
    width: 1200px;
    height: 689px;
    overflow: hidden;
    background: var(--backdrop);
    font-family: "Open Sans", Arial, sans-serif;
  }
  .sheet {
    position: relative;
    width: 1200px;
    height: 689px;
    display: flex;
    align-items: center;
    justify-content: center;
    gap: 50px;
  }
  .card {
    position: relative;
    width: 525px;
    height: 300px;
    border-radius: 22px;
    overflow: hidden;
  }
  /* Back side */
  .card--back {
    background: var(--gold);
    display: flex;
    align-items: center;
    justify-content: center;
  }
  .card--back .brand-name {
    color: var(--gold-deep);
    font-size: 58px;
    font-weight: 700;
    letter-spacing: 1px;
  }
  /* Front side */
  .card--front {
    background: var(--paper);
  }
  .card--front .brand-name {
    position: absolute;
    top: 52px;
    left: 0;
    right: 0;
    text-align: center;
    color: var(--navy);
    font-size: 50px;
    font-weight: 700;
    letter-spacing: 1px;
  }
  .details {
    position: absolute;
    left: 0;
    right: 0;
    top: 170px;
    display: flex;
    justify-content: center;
    align-items: stretch;
    gap: 22px;
  }
  .person {
    text-align: right;
    color: var(--ink);
    font-size: 15px;
    line-height: 21px;
  }
  .person__name {
    color: var(--gold);
    font-weight: 700;
    font-size: 21px;
    line-height: 28px;
    letter-spacing: 0.5px;
  }
  .divider {
    width: 2px;
    background: var(--gold);
  }
  .contact {
    list-style: none;
    color: var(--ink);
    font-size: 15px;
    line-height: 25px;
  }
  .contact li {
    display: flex;
    align-items: center;
    gap: 9px;
  }
  .contact svg {
    width: 12px;
    height: 12px;
    fill: var(--gold);
    flex: none;
  }
</style>
</head>
<body>
<main class="sheet">
  <section class="card card--back" aria-label="Card back">
    <span class="brand-name">Heron Mortgage</span>
  </section>

  <section class="card card--front" aria-label="Card front">
    <span class="brand-name">Heron Mortgage</span>
    <div class="details">
      <div class="person">
        <div class="person__name">DANA ELLIS</div>
        <div>Managing Director</div>
        <div>Your address, City</div>
        <div>State, Zip 1234</div>
      </div>
      <div class="divider"></div>
      <ul class="contact">
        <li>
          <svg viewBox="0 0 12 12" aria-hidden="true"><path d="M2.5 1l2 2.2-1 1.3c.7 1.5 1.8 2.6 3.3 3.3l1.3-1 2.2 2-1.2 1.7C5.3 10.5 1.5 6.7 1 2.2z"/></svg>
          <span>123 456 789</span>
        </li>
        <li>
          <svg viewBox="0 0 12 12" aria-hidden="true"><path d="M1 2.5h10v7H1z M1.5 3l4.5 3.5L10.5 3" stroke="#fff" stroke-width="1"/></svg>
          <span>info@yourmail.com</span>
        </li>
        <li>
          <svg viewBox="0 0 12 12" aria-hidden="true"><circle cx="6" cy="6" r="5"/></svg>
          <span>www.yourwebsite.com</span>
        </li>
      </ul>
    </div>
  </section>
</main>
</body>
</html>
```